Lumora Systems New Website - IT Infrastructure | Smart Cabinet | Micro Data Center

We're an IT SI providing Server Room Design & Build | All-in-One Rack & Smart Cabinet | Structured Cabling | IT Relocation | Maintenance. Old website can be found at www.lumorasys.com.hk. We'd like a brand new wix website which is modern, minimalist, interactive with some animation. Website content will be mostly static and include our service, our project, news and events, about us, contacts, blogs, partners and brands, etc.

reference sites:
We'd like to see more designs referring to below

https://www.pixelvane.example/design/41736205
https://www.pixelvane.example/design/41892417
https://velbrinn.example/

Animation (scrolling effect) referring to
https://velbrinn.example/intelligence/smart-office-room/
Updates

we'd like below style.

Designs look the same

Target Market(s)

Commercials in HK

Industry/Entity Type

IT, Technology, Data Center

Coding

Coded - Design and coding required

Font styles to use
Sans Serif

Requirements
Must have
• CMS, Some Interactive Elements/ Graphics

```html
<!DOCTYPE html>
<html lang="en">
<head>
<meta charset="utf-8">
<title>Lumora Systems – IT Infrastructure</title>
<link href="https://fonts.googleapis.com/css2?family=Montserrat:wght@400;500;600;700&display=swap" rel="stylesheet">
<style>
:root{
  --navy:#0f1733;
  --red:#d9382b;
  --ink:#1d2238;
  --body:#3c4152;
  --pink:#fcebea;
  --pink-deep:#f6cfcc;
  --lav:#e9edfb;
  --lav-deep:#c9d4fa;
  --grey:#e6e6e9;
  --white:#ffffff;
}
*{margin:0;padding:0;box-sizing:border-box}
html,body{width:1200px;height:4823px;overflow:hidden}
body{position:relative;background:var(--white);font-family:'Montserrat',sans-serif;color:var(--ink)}
.abs{position:absolute}
.btn{position:absolute;background:var(--navy);color:var(--white);font-weight:600;display:flex;align-items:center;justify-content:center;border-radius:4px;box-shadow:4px 4px 0 -1px var(--white),5px 5px 0 0 var(--red)}
.section-title{position:absolute;left:0;width:1200px;text-align:center;font-size:32px;font-weight:500;color:var(--ink)}
.title-bar{position:absolute;left:572px;width:56px;height:4px;background:linear-gradient(90deg,var(--red) 50%,var(--navy) 50%)}

/* nav */
.hero-blob{position:absolute;left:420px;top:0;width:780px;height:585px;background:var(--lav);border-bottom-left-radius:520px 470px}
.brand{position:absolute;left:112px;top:36px;display:flex;align-items:center;gap:10px;font-size:30px;font-weight:600;color:var(--navy)}
.brand-mark{width:30px;height:30px;border:3px solid var(--navy);border-radius:4px}
.nav{position:absolute;top:48px;left:346px;display:flex;gap:31px;font-size:16px;font-weight:500;color:var(--ink)}
.nav .active{color:var(--red)}
.get-started{left:906px;top:32px;width:182px;height:54px;font-size:19px}

/* hero */
.welcome{left:112px;top:162px;font-size:22px;font-weight:500}
.welcome b{color:var(--red);font-size:36px;font-weight:700}
.tagline{left:109px;top:234px;font-size:22px;color:var(--red)}
.hero-list{left:112px;top:290px;list-style:none;font-size:15px;line-height:38.4px;color:var(--ink)}
.hero-list li::before{content:"»";margin-right:14px;font-weight:700}
.hero-art{left:534px;top:140px;width:590px;height:425px;border-radius:40px;background:linear-gradient(135deg,#c9d5fb,#edf1fd 60%,#f6d8d6)}

/* services */
.svc-card{position:absolute;top:719px;width:330px;height:318px;background:linear-gradient(90deg,#d9d9dc,#f3d4d2);border-radius:34px 0 0 0;text-align:center}
.svc-card.featured{top:706px;height:346px;background:var(--white);border:3px solid var(--navy);border-top-color:var(--red);border-radius:26px 26px 0 0;z-index:2}
.svc-icon{margin:30px auto 0;width:60px;height:66px;display:block}
.svc-card h3{font-size:20px;font-weight:500;line-height:38px;margin-top:10px;padding:0 8px}
.svc-card p{font-size:14.5px;line-height:31px;color:var(--body);padding:0 12px;margin-top:6px}
.svc-arrow{position:absolute;left:50%;bottom:20px;margin-left:-15px;width:30px;height:30px}
.view-services{left:507px;top:1103px;width:182px;height:54px;font-size:18px}

/* about */
.about-bg{position:absolute;left:0;top:1133px;width:1200px;height:610px}
.about-art{left:66px;top:1330px;width:534px;height:336px;border-radius:50% 40% 30% 40%;background:linear-gradient(135deg,#f3c9c5,#e6e7f1 70%)}
.about-title{left:642px;top:1326px;font-size:32px;font-weight:500}
.about-title::after{content:"";position:absolute;left:0;top:56px;width:56px;height:4px;background:linear-gradient(90deg,var(--red) 50%,var(--navy) 50%)}
.about-copy{left:642px;top:1404px;width:450px;font-size:15px;line-height:31px;color:var(--body)}
.read-more{left:642px;top:1642px;width:144px;height:50px;font-size:17px}

/* projects */
.project{position:absolute;top:1928px;width:236px;height:375px;overflow:hidden}
.project-photo{width:100%;height:272px}
.project-caption{position:absolute;left:0;bottom:0;width:100%;height:103px;background:var(--navy);color:var(--white);display:flex;align-items:center;justify-content:center;text-align:center;font-size:15.5px;line-height:25px;font-weight:500;padding:0 10px}
.project-caption .name{font-size:24px;font-weight:500}
.project-caption .pair{display:flex;gap:18px;font-size:14px;line-height:20px}

/* partners */
.badge{position:absolute;width:140px;height:122px;background:var(--white);border-radius:6px;box-shadow:0 3px 12px rgba(20,25,60,.12);display:flex;align-items:center;justify-content:center}
.badge span{display:block;width:88px;height:18px;border-radius:9px;background:#cfd1d8}
.badge.hero-badge{width:224px;height:182px;background:var(--navy);border-radius:8px}
.badge.hero-badge span{width:130px;height:24px;background:#ffffff}

/* blogs */
.blog-bg{position:absolute;left:0;top:2892px;width:1200px;height:790px}
.blog{position:absolute;top:3046px;width:314px}
.blog-img{width:314px;height:254px;background:var(--white)}
.blog-img div{margin:20px auto;width:220px;height:214px;border-radius:30px;background:linear-gradient(135deg,#f7d6d3,#fbeeee 60%,#e9e9f2)}
.blog h4{margin-top:32px;font-size:21px;font-weight:500}
.blog time{display:block;margin-top:20px;font-size:15px}
.blog p{margin-top:14px;font-size:15px;line-height:31px;color:var(--body)}

/* events */
.events-title{left:112px;top:3714px;font-size:32px;font-weight:500}
.events-title::after{content:"";position:absolute;left:0;top:54px;width:56px;height:4px;background:linear-gradient(90deg,var(--red) 50%,var(--navy) 50%)}
.events-copy{left:112px;top:3793px;width:350px;font-size:15px;line-height:31px;color:var(--body)}
.event{position:absolute;top:3678px;width:270px;height:291px;background:var(--white);border-radius:30px 0 0 0;box-shadow:-3px 2px 14px rgba(20,25,60,.14);overflow:hidden}
.event-art{position:absolute;left:20px;top:40px;width:200px;height:150px;border-radius:20px;background:linear-gradient(135deg,#f6cfcb,#fcefee)}
.event-date{position:absolute;right:0;top:0;width:66px;height:58px;background:var(--navy);color:var(--white);text-align:center;font-size:15px;line-height:24px;padding-top:5px}
.event-band{position:absolute;left:0;bottom:0;width:100%;height:54px;background:var(--navy);color:var(--white);display:flex;align-items:center;justify-content:center;font-weight:600;font-size:16px}

/* contact */
.contact{position:absolute;left:0;top:4058px;width:1200px;height:510px;background:var(--navy)}
.map{position:absolute;left:0;top:0;width:459px;height:510px;background:linear-gradient(135deg,#5b5f6c,#3a3e4b 60%,#2f3340)}
.info-card{position:absolute;left:322px;top:55px;width:380px;height:440px;background:var(--white);text-align:center;font-size:15px;color:var(--ink)}
.info-item{position:absolute;left:0;width:100%}
.info-item svg{display:block;margin:0 auto 14px}
.contact-title{position:absolute;left:766px;top:50px;color:var(--white);font-size:29px;font-weight:500}
.field{position:absolute;left:766px;width:357px;height:52px;background:#2a3150;border-radius:6px;color:var(--white);font-size:15px;padding:18px 20px}
.submit{left:874px;top:4476px;width:139px;height:49px;background:var(--white);color:var(--navy);font-size:18px}

/* footer */
.footer{position:absolute;left:0;top:4568px;width:1200px;height:255px;background:var(--navy);color:var(--white)}
.footer .brand{left:522px;top:68px;color:var(--white)}
.footer .brand-mark{border-color:var(--white)}
.footer-nav{position:absolute;top:145px;left:0;width:1200px;display:flex;justify-content:center;gap:30px;font-size:17px;font-weight:500}
.copyright{position:absolute;top:192px;width:1200px;text-align:center;font-size:14px}
.copyright em{font-style:normal;color:var(--red)}
</style>
</head>
<body>

<!-- header -->
<div class="hero-blob"></div>
<div class="brand"><span class="brand-mark"></span>Lumora</div>
<nav class="nav"><span class="active">Home</span><span>About</span><span>Our Services</span><span>Our Projects</span><span>Contact</span></nav>
<div class="btn get-started">Get Started</div>

<!-- hero -->
<div class="abs welcome">Welcome to <b>LUMORA</b></div>
<div class="abs tagline">We're an IT SI providing</div>
<ul class="abs hero-list">
  <li>Server Room Design &amp; Build</li>
  <li>All-in-One Rack &amp; Smart Cabinet</li>
  <li>Structured Cabling</li>
  <li>IT Relocation</li>
  <li>Maintenance</li>
</ul>
<div class="abs hero-art" role="img" aria-label="Isometric illustration of a data center with server racks and engineers at workstations"></div>

<!-- services -->
<h2 class="section-title" style="top:592px">Our Services</h2>
<div class="title-bar" style="top:640px"></div>

<div class="svc-card" style="left:112px">
  <svg class="svc-icon" viewBox="0 0 60 66" fill="none" stroke="#d9382b" stroke-width="2"><path d="M8 30 L40 20 M10 36 L44 30 M14 44 L46 40"/><circle cx="44" cy="34" r="10" stroke="#0f1733"/></svg>
  <h3>Structured Cabling &amp; Fiber Backbone</h3>
  <p>Structured cabling is the design and installation of a cabling</p>
  <svg class="svc-arrow" viewBox="0 0 30 30" fill="none" stroke="#d9382b" stroke-width="2"><circle cx="15" cy="15" r="12"/><path d="M9 15h12M16 10l5 5-5 5"/></svg>
</div>
<div class="svc-card featured" style="left:438px">
  <svg class="svc-icon" viewBox="0 0 60 66" fill="none" stroke="#0f1733" stroke-width="2"><path d="M18 14a12 9 0 0 1 24 0" stroke="#d9382b"/><rect x="8" y="26" width="18" height="34"/><rect x="34" y="26" width="18" height="34"/><path d="M8 36h18M8 46h18M34 36h18M34 46h18"/></svg>
  <h3>Data Center Design &amp; Build</h3>
  <p>Data Center is like a brain to a business deserving and demanding top-level attention and tremendous</p>
  <svg class="svc-arrow" viewBox="0 0 30 30" fill="none" stroke="#d9382b" stroke-width="2"><circle cx="15" cy="15" r="12"/><path d="M9 15h12M16 10l5 5-5 5"/></svg>
</div>
<div class="svc-card" style="left:758px">
  <svg class="svc-icon" viewBox="0 0 60 66" fill="none" stroke="#d9382b" stroke-width="2"><path d="M16 22a10 10 0 0 1 12-12a10 10 0 0 1 18 6a7 7 0 0 1-2 14H18a8 8 0 0 1-2-8z"/><rect x="21" y="34" width="18" height="28" stroke="#0f1733"/><path d="M21 43h18M21 52h18" stroke="#0f1733"/></svg>
  <h3>All-In-One Rack /<br>Micro-Data Center</h3>
  <p>Lumora offers adaptive IT hardware support maintenance service to our</p>
  <svg class="svc-arrow" viewBox="0 0 30 30" fill="none" stroke="#d9382b" stroke-width="2"><circle cx="15" cy="15" r="12"/><path d="M9 15h12M16 10l5 5-5 5"/></svg>
</div>
<div class="btn view-services">View Services</div>

<!-- about -->
<svg class="about-bg" viewBox="0 0 1200 610" preserveAspectRatio="none">
  <path d="M0 0 C300 120 800 120 1200 40 L1200 610 L0 610Z" fill="#f8d9d6"/>
  <path d="M0 40 C300 150 800 140 1200 60 L1200 610 L0 610Z" fill="#fcebea"/>
</svg>
<div class="abs about-art" role="img" aria-label="Isometric illustration of an engineer at a server room control desk"></div>
<h2 class="abs about-title">About Lumora Systems</h2>
<p class="abs about-copy">Lumora Systems is well experienced in delivering the best in Data Center Infrastructure, Network Infrastructure, Structured Cabling, Telephony, Access Control, Video Surveillance, Audiovisual &amp;Conferencing, Relocation &amp; Migration and Maintenance solutions. Our dedication, focus, and expertise wins much recognition of many IT professionals in all industries in the region.</p>
<div class="btn read-more">Read More</div>

<!-- projects -->
<h2 class="section-title" style="top:1818px">Our Projects</h2>
<div class="title-bar" style="top:1868px"></div>

<div class="project" style="left:112px">
  <div class="project-photo" role="img" aria-label="Photo of blue patch cables in a server rack" style="background:linear-gradient(90deg,#1d4f9c,#3b7bd4 50%,#2a2f3a)"></div>
  <div class="project-caption">A renowned china based listed insurance company</div>
</div>
<div class="project" style="left:358px">
  <div class="project-photo" role="img" aria-label="Photo of dense blue network cabling on patch panels" style="background:linear-gradient(180deg,#2f66b8,#5c95de 50%,#233a66)"></div>
  <div class="project-caption"><span class="name">Tradewell Links</span></div>
</div>
<div class="project" style="left:605px">
  <div class="project-photo" role="img" aria-label="Photo of black server cabinets in a data hall" style="background:linear-gradient(90deg,#3a3f48,#15181d 50%,#4a505a)"></div>
  <div class="project-caption"><div class="pair"><span>Harbour Crest<br>Bank</span><span>Meridian<br>Assurance</span></div></div>
</div>
<div class="project" style="left:852px">
  <div class="project-photo" role="img" aria-label="Photo of a smart cabinet with a touch display panel" style="background:linear-gradient(135deg,#4a5058,#22262c 60%,#5a616b)"></div>
  <div class="project-caption">A renowned china based listed securities firm</div>
</div>

<!-- partners -->
<h2 class="section-title" style="top:2378px">Our Partners</h2>
<div class="title-bar" style="top:2428px"></div>

<div class="badge" style="left:-40px;top:2518px"><span></span></div>
<div class="badge" style="left:130px;top:2518px"><span></span></div>
<div class="badge" style="left:310px;top:2518px"><span></span></div>
<div class="badge hero-badge" style="left:487px;top:2486px"><span></span></div>
<div class="badge" style="left:740px;top:2518px"><span></span></div>
<div class="badge" style="left:917px;top:2518px"><span></span></div>
<div class="badge" style="left:1080px;top:2518px"><span></span></div>

<div class="badge" style="left:-48px;top:2686px"><span></span></div>
<div class="badge" style="left:158px;top:2686px"><span></span></div>
<div class="badge" style="left:337px;top:2686px"><span></span></div>
<div class="badge" style="left:517px;top:2686px"><span></span></div>
<div class="badge" style="left:695px;top:2686px"><span></span></div>
<div class="badge" style="left:874px;top:2686px"><span></span></div>
<div class="badge" style="left:1056px;top:2686px"><span></span></div>

<!-- blogs -->
<svg class="blog-bg" viewBox="0 0 1200 790" preserveAspectRatio="none">
  <path d="M0 0 H1200 V790 C850 730 350 705 0 720Z" fill="#c9d4fa"/>
  <path d="M0 0 H1200 V762 C850 702 350 690 0 705Z" fill="#e9edfb"/>
</svg>
<h2 class="section-title" style="top:2930px">Latest Blogs</h2>
<div class="title-bar" style="top:2980px"></div>

<article class="blog" style="left:112px">
  <div class="blog-img"><div role="img" aria-label="Isometric illustration of a database server and laptop"></div></div>
  <h4>Sed ut perspiciatis unde</h4><time>24th June 2023</time>
  <p>Lorem ipsum dolor sit amet, consectetur adipiscing elit, sed do eiusmod tempor incididunt.</p>
</article>
<article class="blog" style="left:442px">
  <div class="blog-img"><div role="img" aria-label="Isometric illustration of a connected smart city"></div></div>
  <h4>Sed ut perspiciatis unde</h4><time>15th May 2023</time>
  <p>Lorem ipsum dolor sit amet, consectetur adipiscing elit, sed do eiusmod tempor incididunt.</p>
</article>
<article class="blog" style="left:771px">
  <div class="blog-img"><div role="img" aria-label="Isometric illustration of cloud servers on a platform"></div></div>
  <h4>Sed ut perspiciatis unde</h4><time>06th April 2023</time>
  <p>Lorem ipsum dolor sit amet, consectetur adipiscing elit, sed do eiusmod tempor incididunt.</p>
</article>

<!-- events -->
<h2 class="abs events-title">Upcoming Events</h2>
<p class="abs events-copy">Neque porro quisquam est, qui dolorem ipsum quia dolor sit amet, consectetur, adipisci velit, sed quia non numquam eius modi tempora incidunt ut labore et dolore magnam aliquam quaerat.</p>
<div class="event" style="left:517px">
  <div class="event-art" role="img" aria-label="Isometric illustration of an office floor plan"></div>
  <div class="event-date">April<br>06</div>
  <div class="event-band">Lorem ipsum dolor sit</div>
</div>
<div class="event" style="left:816px">
  <div class="event-art" role="img" aria-label="Isometric illustration of a security shield over a network"></div>
  <div class="event-date">June<br>26</div>
  <div class="event-band">Lorem ipsum dolor sit</div>
</div>

<!-- contact -->
<section class="contact">
  <div class="map" role="img" aria-label="Street map of Kowloon with the office location pinned"></div>
  <div class="info-card">
    <div class="info-item" style="top:34px">
      <svg width="20" height="20" viewBox="0 0 24 24" fill="#d9382b"><path d="M6.6 10.8a15 15 0 0 0 6.6 6.6l2.2-2.2a1 1 0 0 1 1-.25 11.4 11.4 0 0 0 3.6.57 1 1 0 0 1 1 1V20a1 1 0 0 1-1 1A17 17 0 0 1 3 4a1 1 0 0 1 1-1h3.5a1 1 0 0 1 1 1c0 1.25.2 2.45.57 3.57a1 1 0 0 1-.25 1z"/></svg>
      +852 2760 4410 / +852 5938 1174
    </div>
    <div class="info-item" style="top:118px">
      <svg width="22" height="22" viewBox="0 0 24 24" fill="none" stroke="#d9382b" stroke-width="2"><rect x="6" y="3" width="12" height="6"/><rect x="3" y="9" width="18" height="8" rx="1"/><rect x="7" y="14" width="10" height="7"/></svg>
      +852 2760 4411
    </div>
    <div class="info-item" style="top:200px">
      <svg width="22" height="18" viewBox="0 0 24 18" fill="#d9382b"><path d="M0 0h24v18H0z"/><path d="M1 1l11 9 11-9" stroke="#fff" stroke-width="2" fill="none"/></svg>
      hello@lumorasys.com.hk
    </div>
    <div class="info-item" style="top:284px;line-height:30px;font-size:14px">
      <svg width="18" height="22" viewBox="0 0 18 24" fill="#d9382b"><path d="M9 0a9 9 0 0 1 9 9c0 6-9 15-9 15S0 15 0 9a9 9 0 0 1 9-9z"/><circle cx="9" cy="9" r="3.5" fill="#fff"/></svg>
      Rm 905, 9/F, Harbourline Centre, 18 Kwun Lam Road,<br>Kwun Tong, Kowloon, Hong Kong
    </div>
  </div>
  <h2 class="contact-title">Contact Us</h2>
</section>
<div class="field" style="top:4175px">Name</div>
<div class="field" style="top:4235px">Email Address</div>
<div class="field" style="top:4295px">Mobile Number</div>
<div class="field" style="top:4355px;height:97px">Message</div>
<div class="btn submit">Submit</div>

<!-- footer -->
<footer class="footer">
  <div class="brand"><span class="brand-mark"></span>Lumora</div>
  <nav class="footer-nav"><span>Home</span><span>About</span><span>Our Services</span><span>Our Projects</span><span>Contact</span></nav>
  <p class="copyright">© 2023 by <em>Lumora</em>. All Rights Reserved.</p>
</footer>

</body>
</html>
```